Business Card for Marriage Commissioner

I am a marriage commissioner in the province of Alberta, meaning that I perform civil unions here. I have been trying to think of a unique design for my business card, something a bit different. A lot of "unique" designs seem to incorporate unique cuts or "some assembly required" or printed on plastic or meat. I would like my design to be a full colour card that is a typical business card size.

The information on the card should have:
Lou Varnick
my occupation: Marriage Commissioner
my website: www.louvarnick.ca
my e-mail: lou@louvarnick.ca
my phone: 780-419-8206

I originally submitted a design to the printer that had a screen capture of a findwell search window, with my name and occupation in the text box. And underneath that, my phone number. Nothing else. They indicated they could not print this because it was a copyright violation.

One option on the design is I am a retired chemist-so a chemistry themed card would also be of interest, as long as it isn't a "Lamp Season" theme, as I have that on my other business cards already...

I would prefer a single sided card, but I am open to a double sided card if it is clever!

I would also prefer not to have pictures of male and female couples as in my position I will also marry same sex couples. Same thing for male/female symbols. Someone has submitted two graduated cylinders in love, which is very clever, and gets around this male/female type.

Thanks for your help and interest.

Target Market(s)

Young couples.

Industry/Entity Type

Plastic

Requirements
Nice to have
• chemistry ideas!
Should not have
• Male/female pictures, male/female symbols.
No QR codes.
No transparent designs, will go on paper stock.

```html
<!DOCTYPE html>
<html lang="en">
<head>
<meta charset="utf-8">
<title>Lou Varnick — Marriage Commissioner Business Card</title>
<link rel="stylesheet" href="https://fonts.googleapis.com/css2?family=Marcellus&family=Open+Sans:wght@400&display=swap">
<style>
  :root {
    --page: #ffffff;
    --charcoal: #252422;
    --sand: #e6d594;
    --gold: #cdb978;
    --gold-light: #e4d08f;
    --ivory: #f3efe2;
    --teal: #5bc5d0;
    --white: #ffffff;
  }
  html, body {
    margin: 0;
    padding: 0;
    width: 1200px;
    height: 1200px;
    overflow: hidden;
    background: var(--page);
  }
  .card {
    position: absolute;
    left: 328px;
    top: 76px;
    width: 544px;
    height: 951px;
    border-radius: 28px;
    overflow: hidden;
    background: var(--sand);
  }
  .band {
    position: absolute;
    left: 0;
    width: 100%;
    background: var(--charcoal);
  }
  .band--top { top: 0; height: 146px; }
  .band--bottom { top: 807px; height: 144px; }
  .rule {
    position: absolute;
    left: 0;
    width: 100%;
    height: 2px;
    background: var(--charcoal);
  }
  .website-label {
    position: absolute;
    top: 62px;
    width: 100%;
    text-align: center;
    font-family: "Open Sans", sans-serif;
    font-size: 20px;
    color: var(--ivory);
    letter-spacing: 0.5px;
  }
  .website-url {
    position: absolute;
    top: 90px;
    width: 100%;
    text-align: center;
    font-family: "Marcellus", serif;
    font-size: 26px;
    color: var(--gold);
    letter-spacing: 0.5px;
  }
  .seal {
    position: absolute;
    left: 80px;
    top: 285px;
    width: 384px;
    height: 384px;
  }
  .seal-name {
    position: absolute;
    top: 438px;
    width: 100%;
    text-align: center;
    font-family: "Marcellus", serif;
    font-size: 47px;
    color: var(--gold-light);
    letter-spacing: 0.5px;
  }
  .seal-title {
    position: absolute;
    top: 490px;
    width: 100%;
    text-align: center;
    font-family: "Marcellus", serif;
    font-size: 20px;
    color: var(--gold);
  }
  .ribbon {
    position: absolute;
    left: 58px;
    top: 836px;
    width: 428px;
    height: 78px;
  }
  .contact {
    position: absolute;
    width: 100%;
    text-align: center;
    color: var(--white);
    font-family: "Marcellus", serif;
  }
  .contact--email { top: 846px; font-size: 27px; }
  .contact--phone { top: 882px; font-size: 19px; }
  .contact-tag { font-size: 18px; margin-right: 6px; }
  .contact--phone .contact-tag { font-size: 17px; }
</style>
</head>
<body>
  <div class="card">
    <div class="band band--top"></div>
    <div class="rule" style="top:147px"></div>
    <div class="rule" style="top:151px"></div>

    <div class="website-label">..... Website .....</div>
    <div class="website-url">WWW.LOUVARNICK.CA</div>

    <svg class="seal" viewBox="0 0 384 384" aria-hidden="true">
      <circle cx="192" cy="192" r="192" fill="var(--charcoal)"/>
      <circle cx="192" cy="192" r="183" fill="none" stroke="var(--ivory)" stroke-width="1.5"/>
      <circle cx="192" cy="192" r="176" fill="none" stroke="var(--ivory)" stroke-width="1" stroke-dasharray="4 4" opacity="0.7"/>
    </svg>
    <svg style="position:absolute;left:188px;top:368px;width:168px;height:48px" viewBox="0 0 168 48" role="img" aria-label="Gold flourish ornament above the name">
      <rect x="0" y="6" width="168" height="36" rx="18" fill="var(--gold-light)"/>
    </svg>
    <svg style="position:absolute;left:188px;top:528px;width:168px;height:48px" viewBox="0 0 168 48" role="img" aria-label="Gold flourish ornament below the title">
      <rect x="0" y="6" width="168" height="36" rx="18" fill="var(--gold-light)"/>
    </svg>
    <div class="seal-name">LOU VARNICK</div>
    <div class="seal-title">MARRIAGE COMMISSIONER</div>

    <div class="rule" style="top:800px"></div>
    <div class="rule" style="top:804px"></div>
    <div class="band band--bottom"></div>

    <svg class="ribbon" viewBox="0 0 428 78" aria-hidden="true">
      <path d="M28 0 H400 L428 39 L400 78 H28 L0 39 Z" fill="var(--teal)"/>
    </svg>
    <div class="contact contact--email"><span class="contact-tag">(E):</span>LOU@LOUVARNICK.CA</div>
    <div class="contact contact--phone"><span class="contact-tag">(P):</span>780-419-8206</div>
  </div>
</body>
</html>
```